Brenlow Estates Website and Logo Design

We need a new logo and website designed for 'Brenlow Estates Ltd', which is a well established Guernsey property holding company founded in 1934.

The company does not currently have a website. The new website should be similar in style and layout to https://www.quorvanhall.example/.

Target Market(s)

Industry, Media, Tenants

Industry/Entity Type

Property Management

Logo Text

BEL OR Brenlow Estates Ltd OR BE

Coding

Coded - Design and coding required

Number of Pages Required

4 page

Font styles to use
Other font styles liked:
• Helvetica

Requirements
Must have
• The logo laying over the picture (like https://www.quorvanhall.example/).
• Big pictures on homepage (like https://www.quorvanhall.example/)

```html
<!DOCTYPE html>
<html lang="en">
<head>
<meta charset="utf-8">
<title>Brenlow Estates Limited</title>
<link rel="stylesheet" href="https://fonts.googleapis.com/css2?family=Raleway:wght@400;500;600;700&family=Open+Sans:wght@400;600&family=Lora:ital@1&display=swap">
<style>
  :root {
    --navy: #1d3f8f;
    --navy-deep: #173476;
    --red: #c8102e;
    --ink: #2b2b2b;
    --body: #555;
    --rule: #e2e2e2;
    --soft: #f6f6f6;
    --white: #fff;
  }
  * { box-sizing: border-box; margin: 0; padding: 0; }
  html, body { width: 1200px; height: 2875px; overflow: hidden; }
  body { font-family: "Open Sans", Helvetica, Arial, sans-serif; color: var(--body); background: var(--white); position: relative; }
  section, header, footer { position: absolute; left: 0; width: 1200px; }
  .abs { position: absolute; }
  .heading { font-family: "Raleway", Helvetica, sans-serif; color: var(--ink); font-weight: 500; text-align: center; width: 1200px; left: 0; font-size: 32px; }
  .btn { position: absolute; border: 2px solid currentColor; border-radius: 20px; font-family: "Raleway", sans-serif; font-weight: 700; font-size: 11px; text-transform: uppercase; display: flex; align-items: center; justify-content: center; }

  /* Hero */
  .hero { top: 0; height: 600px; background: linear-gradient(180deg, #3d5fa8 0%, #7a94c4 14%, #9a9b92 24%, #5d6b6c 34%, #2f5a6e 48%, #1f4f5e 70%, #2c6a78 100%); }
  .brand { left: 160px; top: 30px; display: flex; align-items: center; gap: 10px; }
  .brand-mark { width: 34px; height: 34px; border: 2px solid var(--white); border-radius: 50%; }
  .brand-name { font-family: "Raleway", sans-serif; font-weight: 600; font-size: 15px; color: var(--white); line-height: 1.15; letter-spacing: .5px; }
  .nav { left: 425px; top: 36px; display: flex; gap: 0; align-items: center; }
  .nav a { color: var(--white); text-decoration: none; font-family: "Raleway", sans-serif; font-size: 14px; margin-right: 46px; }
  .nav .donate { border: 1.5px solid var(--white); border-radius: 16px; padding: 5px 16px; margin-right: 0; margin-left: -6px; }
  .arrow { top: 290px; }
  .hero-tag { top: 352px; width: 1200px; text-align: center; font-family: "Lora", serif; font-style: italic; color: var(--white); font-size: 22px; letter-spacing: 1px; }
  .hero-title { top: 396px; width: 1200px; text-align: center; font-family: "Raleway", sans-serif; font-weight: 700; color: var(--white); font-size: 40px; letter-spacing: 1px; }

  /* Welcome */
  .welcome { top: 600px; height: 307px; border-bottom: 1px solid var(--rule); }
  .welcome .heading { top: 50px; }
  .welcome p { left: 182px; top: 114px; width: 844px; text-align: center; font-size: 10.5px; line-height: 16.3px; color: #444; }
  .welcome .btn { left: 546px; top: 224px; width: 106px; height: 35px; color: var(--navy); }

  /* Property */
  .property { top: 907px; height: 554px; background: var(--soft); border-bottom: 1px solid var(--rule); }
  .property .heading { top: 38px; }
  .card { top: 111px; width: 274px; }
  .card-photo { width: 274px; height: 203px; border: 4px solid var(--white); outline: 1px solid #9fb0d6; }
  .p1 { background: linear-gradient(180deg, #6d8fc4 0%, #a8bfdf 45%, #3e6a9a 60%, #2e5f8f 100%); }
  .p2 { background: linear-gradient(180deg, #5b7fbd 0%, #9fb8dc 35%, #a5a39a 58%, #3f6f8e 78%, #3a6c90 100%); }
  .p3 { background: linear-gradient(180deg, #7f9ed0 0%, #b4c7e4 38%, #4f7fa0 58%, #2e6283 100%); }
  .card h3 { margin-top: 26px; font-family: "Raleway", sans-serif; font-weight: 400; font-size: 21px; color: #333; }
  .card p { margin-top: 12px; font-size: 10.5px; line-height: 21px; color: #555; }
  .card .btn { position: relative; margin-top: 22px; width: 108px; height: 37px; color: var(--red); }

  /* What we do */
  .services { top: 1461px; height: 485px; }
  .services .heading { top: 38px; }
  .services .intro { left: 240px; top: 92px; width: 720px; text-align: center; font-size: 10.5px; line-height: 21px; }
  .service { top: 175px; width: 200px; text-align: center; }
  .ring { width: 124px; height: 124px; margin: 0 auto; border: 2px solid var(--navy); border-radius: 50%; padding: 7px; }
  .ring-inner { width: 100%; height: 100%; border: 2px solid var(--navy); border-radius: 50%; display: flex; align-items: center; justify-content: center; }
  .service h4 { margin-top: 32px; font-family: "Raleway", sans-serif; font-weight: 500; font-size: 17px; color: #333; }
  .service p { margin-top: 16px; font-size: 10.5px; line-height: 20px; }

  /* Banner */
  .banner { top: 1946px; height: 264px; background: linear-gradient(180deg, #6b7b93 0%, #8592a3 22%, #4a5a55 38%, #3d5b6a 55%, #2f4f62 100%); }
  .banner p { top: 82px; width: 1200px; text-align: center; font-family: "Raleway", sans-serif; color: var(--white); font-size: 32px; line-height: 42px; }

  /* News */
  .news { top: 2210px; height: 412px; }
  .news .heading { top: 72px; }
  .post { top: 172px; width: 260px; }
  .date { position: absolute; left: 0; top: 0; color: var(--red); font-family: "Raleway", sans-serif; padding-right: 12px; border-right: 1px solid var(--rule); height: 44px; }
  .date .m { font-size: 14px; line-height: 16px; }
  .date .d { font-size: 24px; font-weight: 700; line-height: 24px; }
  .post h5 { position: absolute; left: 63px; top: 0; width: 200px; font-family: "Raleway", sans-serif; font-weight: 600; font-size: 15px; line-height: 23px; color: #222; }
  .post p { position: absolute; left: 0; top: 72px; width: 260px; font-size: 10.5px; line-height: 19.5px; }

  /* Footer */
  .footer { top: 2622px; height: 253px; background: linear-gradient(180deg, var(--navy) 0%, var(--navy-deep) 100%); border-top: 4px solid var(--red); color: #dce4f5; font-size: 10.5px; }
  .footer .brand { top: 68px; left: 161px; }
  .footer .brand-mark { width: 30px; height: 30px; }
  .footer .about { left: 161px; top: 118px; width: 220px; line-height: 19px; }
  .footer .copy { left: 161px; top: 196px; }
  .col { top: 56px; padding-left: 0; }
  .col h6 { font-family: "Raleway", sans-serif; font-weight: 600; font-size: 14px; color: var(--white); margin-bottom: 10px; }
  .col li { list-style: none; line-height: 20px; }
  .divider { top: 60px; width: 1px; height: 160px; background: rgba(255,255,255,.18); }
  .social { display: flex; gap: 6px; margin-top: 12px; }
  .social span { width: 34px; height: 34px; border: 1.5px solid var(--white); border-radius: 50%; }
  .page-code { right: 100px; top: 216px; font-size: 10px; }
</style>
</head>
<body>

<header class="hero" role="img" aria-label="Harbour scene with moored boats and a waterfront town on the hillside">
  <div class="abs brand"><span class="brand-mark"></span><span class="brand-name">BRENLOW ESTATES<br>LIMITED</span></div>
  <nav class="abs nav">
    <a href="#">Home</a><a href="#">About</a><a href="#">News</a><a href="#">Research</a><a href="#">Videos</a><a href="#">Events</a><a href="#">Blog</a><a href="#" class="donate">Donate</a>
  </nav>
  <svg class="abs arrow" style="left:32px" width="20" height="34" viewBox="0 0 20 34"><path d="M16 3 3 17l13 14" fill="none" stroke="#fff" stroke-width="4"/></svg>
  <svg class="abs arrow" style="left:1148px" width="20" height="34" viewBox="0 0 20 34"><path d="M4 3l13 14L4 31" fill="none" stroke="#fff" stroke-width="4"/></svg>
  <div class="abs hero-tag">Lorem ipsum dolor sit ametonsectetur</div>
  <h1 class="abs hero-title">BRENLOW ESTATES LIMITED</h1>
</header>

<section class="welcome">
  <h2 class="abs heading">Welcome to Brenlow Estates Limited</h2>
  <p class="abs">Brenlow Estates Limited (BEL) is a family-owned Guernsey property holding company. It purchases properties that are considered to have potential for development either through refurbishment or by obtaining planning permission to change its classification from, for example, industrial premises to offices or retail outlets, or by the marriage value of buying an adjacent property to one already owned by BEL. BEL's reputation as a fair-minded landlord stems from the application of the founder's tenet of working with the tenant to help maximise the business benefits of both parties. There is no capital gains tax on the sale of property in the Island which makes buying</p>
  <a class="btn" href="#">Read More</a>
</section>

<section class="property">
  <h2 class="abs heading">Our Property</h2>
  <article class="abs card" style="left:161px">
    <div class="card-photo p1" role="img" aria-label="Small boats moored in a rocky bay"></div>
    <h3>Bonorum et Malorum</h3>
    <p>Sd ut perspiciatis unde omnis iste natus error sitp tatem accusantium dolormqu e laudan tium, tote maperiam, eaque ipsa quae ab illo inventore.</p>
    <a class="btn" href="#">Read More</a>
  </article>
  <article class="abs card" style="left:464px">
    <div class="card-photo p2" role="img" aria-label="Harbour town viewed across the water"></div>
    <h3>Bonorum et Malorum</h3>
    <p>Sd ut perspiciatis unde omnis iste natus error sitp tatem accusantium dolormqu e laudan tium, tote maperiam, eaque ipsa quae ab illo inventore.</p>
    <a class="btn" href="#">Read More</a>
  </article>
  <article class="abs card" style="left:765px">
    <div class="card-photo p3" role="img" aria-label="Marina pontoon with an island on the horizon"></div>
    <h3>Bonorum et Malorum</h3>
    <p>Sd ut perspiciatis unde omnis iste natus error sitp tatem accusantium dolormqu e laudan tium, tote maperiam, eaque ipsa quae ab illo inventore.</p>
    <a class="btn" href="#">Read More</a>
  </article>
</section>

<section class="services">
  <h2 class="abs heading">What We Do</h2>
  <p class="abs intro">Sed ut perspiciatis unde omnis iste natus error sitolu ptatem accusantium doloremque laudantium, totme maperiam, eaque ipsa quae ab illo inventore veritati quasi architecto beatae vitae dicta suSed ut perspiciatis unde omnis iste natus error sitolu ptatem accusantium dolore.</p>

  <div class="abs service" style="left:159px">
    <div class="ring"><div class="ring-inner">
      <svg width="36" height="32" viewBox="0 0 24 21"><path d="M12 21 2 11A5.6 5.6 0 0 1 12 3.5 5.6 5.6 0 0 1 22 11Z" fill="#c8102e"/></svg>
    </div></div>
    <h4>Finibus Bonorum</h4>
    <p>Sed ut perspiciatis unde omnis isnat us error sitolu ptatem accusantium dolo remque laudantium, totmeloum.</p>
  </div>
  <div class="abs service" style="left:387px">
    <div class="ring"><div class="ring-inner">
      <svg width="32" height="32" viewBox="0 0 24 24"><rect x="2" y="10" width="5" height="12" fill="#c8102e"/><path d="M9 10l4-8c2 0 3 1 2.6 3L15 9h5.5c1.5 0 2.3 1.3 2 2.5l-2 8.5c-.3 1.2-1.2 2-2.4 2H9Z" fill="#c8102e"/></svg>
    </div></div>
    <h4>Finibus Bonorum</h4>
    <p>Sed ut perspiciatis unde omnis isnat us error sitolu ptatem accusantium dolo remque laudantium, totmeloum.</p>
  </div>
  <div class="abs service" style="left:615px">
    <div class="ring"><div class="ring-inner">
      <svg width="36" height="36" viewBox="0 0 24 24"><circle cx="12" cy="12" r="8.5" fill="none" stroke="#c8102e" stroke-width="5"/><path d="M12 1v6M12 17v6M1 12h6M17 12h6" stroke="#fff" stroke-width="2"/></svg>
    </div></div>
    <h4>Finibus Bonorum</h4>
    <p>Sed ut perspiciatis unde omnis isnat us error sitolu ptatem accusantium dolo remque laudantium, totmeloum.</p>
  </div>
  <div class="abs service" style="left:843px">
    <div class="ring"><div class="ring-inner">
      <svg width="36" height="36" viewBox="0 0 24 24"><path d="M2 3v8l11 11 9-9L11 2H3Z" fill="#c8102e"/><circle cx="7" cy="7" r="2" fill="#fff"/></svg>
    </div></div>
    <h4>Finibus Bonorum</h4>
    <p>Sed ut perspiciatis unde omnis isnat us error sitolu ptatem accusantium dolo remque laudantium, totme mape.</p>
  </div>
</section>

<section class="banner" role="img" aria-label="Harbour entrance with a headland across the sea">
  <p class="abs">At vero eos et accusamus et iustoodi<br>dignissimos ducimuloreui blanditiis</p>
</section>

<section class="news">
  <h2 class="abs heading">Latest News</h2>
  <article class="abs post" style="left:161px">
    <div class="date"><div class="m">DEC</div><div class="d">02</div></div>
    <h5>Sed ut perspiciatis ndois iste natus error sit olupt.</h5>
    <p>Sd ut perspiciatis unde omnis isteiste natus errort vo luptatem accusantium doloremque lisS ut pertis un de omnis isteiste natus Sed ut persluptatem us antium doloremque lisS ut persciatis un.</p>
  </article>
  <article class="abs post" style="left:475px">
    <div class="date"><div class="m">DEC</div><div class="d">02</div></div>
    <h5>Sed ut perspiciatisdomis iste natus error sit olupt.</h5>
    <p>Sd ut perspiciatis unde omnis isteiste natus errort vo luptatem accusantium doloremque lisS ut pertis un de omnis isteiste natus Sed ut persluptatem us antium doloremque lisS ut persciatis un.</p>
  </article>
  <article class="abs post" style="left:790px">
    <div class="date"><div class="m">DEC</div><div class="d">02</div></div>
    <h5>Sed ut perspiciatisdomis iste natus error sit olupt.</h5>
    <p>Sd ut perspiciatis unde omnis isteiste natus errort vo luptatem accusantium doloremque lisS ut pertis un de omnis isteiste natus Sed ut persluptatem us antium doloremque lisS ut persciatis un.</p>
  </article>
</section>

<footer class="footer">
  <div class="abs brand"><span class="brand-mark"></span><span class="brand-name">BRENLOW ESTATES<br>LIMITED</span></div>
  <p class="abs about">Sed ut perspiciatis unde omnis tatem acc usa ntiudoloremque laloren tiumtotadper tspic ia tilos untate mcustiudolorem</p>
  <p class="abs copy">© 2016 All Copyrights are Reserved.</p>

  <div class="abs divider" style="left:393px"></div>
  <div class="abs col" style="left:443px"><h6>Services</h6><ul><li>At vero eoet accu</li><li>Samus et iusto odio</li><li>Dgnissamus et iusto</li><li>At vero eoet accu</li><li>Samus et iusto odio</li><li>Dgnissamus</li></ul></div>
  <div class="abs divider" style="left:585px"></div>
  <div class="abs col" style="left:617px"><h6>Links</h6><ul><li>Privacy Policy</li><li>Copyright</li><li>Cookies</li><li>Terms of Use</li><li>Disclaimer</li><li>Legal</li></ul></div>
  <div class="abs divider" style="left:718px"></div>
  <div class="abs col" style="left:748px"><h6>Company</h6><ul><li>Home</li><li>About us</li><li>Projects</li><li>Donate</li><li>Contact us</li></ul></div>
  <div class="abs divider" style="left:852px"></div>
  <div class="abs col" style="left:880px"><h6>Help &amp; Contact</h6><ul><li>Phone number 1-888-555-0142</li><li>Monday - Friday, 9am - 5pm</li></ul>
    <div class="social"><span></span><span></span><span></span><span></span></div>
  </div>
  <span class="abs page-code">C4</span>
</footer>

</body>
</html>
```